Q&J RESTORATION

I want a brochure similiar to the example i've attached.
My company name is Q&J Restoration. The website is: Q-J-Restoration.example.
The phone number is 919.555.0147.

I don't like the "yellow" being the main color of the example so I'm open to suggestions. I want something CLEAN & Simple, like our logo . This will be a bi fold brochure

```html
<!DOCTYPE html>
<html lang="en">
<head>
<meta charset="utf-8">
<title>Q &amp; J Restoration — Bi-fold Brochure</title>
<link href="https://fonts.googleapis.com/css2?family=Outfit:wght@400;500;600&display=swap" rel="stylesheet">
<style>
  :root {
    --brand-blue: #2b72e0;
    --brand-blue-deep: #2a6bd6;
    --ink: #141414;
    --panel-light: #eceef1;
    --panel-mid: #dcdfe4;
    --photo-dark: #2c3f6b;
    --photo-light: #8a9bb8;
    --blueprint-light: #f2f2f2;
    --blueprint-mid: #bdbdbd;
    --white: #ffffff;
  }
  * { box-sizing: border-box; margin: 0; padding: 0; }
  html, body { width: 1200px; height: 771px; overflow: hidden; background: var(--white); }
  body { font-family: "Outfit", sans-serif; color: var(--ink); }

  .brochure { position: relative; width: 1200px; height: 771px; overflow: hidden; }

  /* Inside left panel */
  .panel-about {
    position: absolute; left: 0; top: 0; width: 599px; height: 771px;
    background: linear-gradient(180deg, var(--panel-light) 0%, #e4e6ea 55%, var(--panel-mid) 100%);
  }
  .panel-about::after {
    content: ""; position: absolute; left: 0; bottom: 0; width: 599px; height: 4px;
    background: var(--brand-blue);
  }
  .wordmark {
    position: absolute; left: 35px; top: 46px;
    font-size: 26px; font-weight: 500; letter-spacing: 0.5px; color: var(--ink);
  }
  .section-label {
    position: absolute; left: 55px; top: 164px; font-size: 18px; font-weight: 400;
  }
  .section-rule {
    position: absolute; left: 0; top: 176px; width: 33px; height: 1px; background: var(--brand-blue);
  }
  .headline {
    position: absolute; left: 32px; top: 188px; font-size: 35px; font-weight: 500; letter-spacing: -0.3px;
  }
  .headline .accent { color: var(--brand-blue); font-weight: 600; }
  .intro {
    position: absolute; left: 34px; top: 243px; width: 520px;
    font-size: 13px; line-height: 20px; font-weight: 400;
  }
  .features { position: absolute; left: 34px; top: 322px; width: 530px; height: 102px; }
  .feature { position: absolute; display: flex; align-items: center; }
  .feature-icon {
    width: 41px; height: 41px; background: var(--brand-blue);
    display: flex; align-items: center; justify-content: center;
  }
  .feature-name { margin-left: 19px; font-size: 15.5px; font-weight: 400; }
  .feature.inspection { left: 0; top: 0; }
  .feature.settlement { left: 228px; top: 0; }
  .feature.one-roof { left: 0; top: 60px; }
  .feature.craftsmanship { left: 228px; top: 60px; }

  .blueprint-photo {
    position: absolute; left: 34px; top: 449px; width: 530px; height: 213px;
    background: linear-gradient(135deg, var(--blueprint-light) 0%, #d6d6d6 45%, var(--blueprint-mid) 70%, #ebebeb 100%);
  }
  .contact-bar {
    position: absolute; left: 33px; top: 690px; width: 533px; height: 41px;
    border: 1px solid var(--brand-blue); display: flex;
  }
  .contact-item { display: flex; align-items: center; font-size: 16.5px; font-weight: 400; }
  .contact-item.phone { width: 211px; padding-left: 32px; border-right: 1px solid var(--brand-blue); }
  .contact-item.web { padding-left: 45px; }
  .contact-item svg { margin-right: 17px; }

  /* Inside right panel */
  .panel-cover {
    position: absolute; left: 599px; top: 0; width: 601px; height: 771px;
    background: var(--brand-blue); overflow: hidden;
  }
  .panel-cover svg { position: absolute; left: 0; top: 0; }
</style>
</head>
<body>
<main class="brochure">
  <section class="panel-about">
    <div class="wordmark">Q &amp; J Restoration</div>

    <span class="section-rule"></span>
    <h2 class="section-label">About Us</h2>
    <h1 class="headline">Q &amp; J <span class="accent">Restoration</span></h1>
    <p class="intro">Lorem Ipsum is simply dummy text of the printing and typesetting industry. Lorem Ipsum has been the industry's standard dummy text ever since the 1500s, when an unknown printer .</p>

    <div class="features">
      <div class="feature inspection">
        <div class="feature-icon">
          <svg width="22" height="22" viewBox="0 0 22 22" fill="#fff">
            <rect x="2" y="7" width="12" height="4" rx="1"/>
            <rect x="7" y="4" width="3" height="4"/>
            <rect x="5" y="3" width="7" height="2" rx="1"/>
            <rect x="12" y="7" width="3" height="6"/>
            <path d="M15.5 15 q2 3 0 4.5 q-2 -1.5 0 -4.5z"/>
          </svg>
        </div>
        <span class="feature-name">Adjuster Inspection</span>
      </div>
      <div class="feature settlement">
        <div class="feature-icon">
          <svg width="22" height="22" viewBox="0 0 22 22" fill="none" stroke="#fff" stroke-width="2">
            <circle cx="11" cy="12" r="7"/>
            <path d="M11 8v4l3 2"/>
            <path d="M9 3h4"/>
          </svg>
        </div>
        <span class="feature-name">Timely Settlement</span>
      </div>
      <div class="feature one-roof">
        <div class="feature-icon">
          <svg width="22" height="22" viewBox="0 0 22 22" fill="none" stroke="#fff" stroke-width="2">
            <path d="M3 11 L11 4 L19 11"/>
            <path d="M5 10v8h12v-8"/>
            <rect x="9" y="13" width="4" height="5"/>
          </svg>
        </div>
        <span class="feature-name">Under One Roof</span>
      </div>
      <div class="feature craftsmanship">
        <div class="feature-icon">
          <svg width="22" height="22" viewBox="0 0 22 22" fill="none" stroke="#fff" stroke-width="2.4" stroke-linecap="round">
            <path d="M4 4 L18 18"/>
            <path d="M18 4 L4 18"/>
          </svg>
        </div>
        <span class="feature-name">Superior Craftsmanship</span>
      </div>
    </div>

    <div class="blueprint-photo" role="img" aria-label="Photograph of rolled architectural blueprints with a wireframe building model"></div>

    <div class="contact-bar">
      <div class="contact-item phone">
        <svg width="18" height="18" viewBox="0 0 24 24" fill="var(--brand-blue)">
          <path d="M6.6 10.8c1.4 2.8 3.8 5.1 6.6 6.6l2.2-2.2c.3-.3.7-.4 1-.2 1.1.4 2.3.6 3.6.6.6 0 1 .4 1 1V20c0 .6-.4 1-1 1C10.6 21 3 13.4 3 4c0-.6.4-1 1-1h3.5c.6 0 1 .4 1 1 0 1.3.2 2.5.6 3.6.1.3 0 .7-.2 1z"/>
        </svg>
        919 555 0147
      </div>
      <div class="contact-item web">
        <svg width="19" height="19" viewBox="0 0 24 24" fill="none" stroke="var(--brand-blue)" stroke-width="1.8">
          <circle cx="12" cy="12" r="10"/>
          <ellipse cx="12" cy="12" rx="4.5" ry="10"/>
          <path d="M2 12h20M4 6.5h16M4 17.5h16"/>
        </svg>
        www.Q-J-Restoration.example
      </div>
    </div>
  </section>

  <section class="panel-cover">
    <svg width="601" height="771" viewBox="0 0 601 771">
      <defs>
        <linearGradient id="floodPhoto" x1="0" y1="0" x2="0" y2="1">
          <stop offset="0" stop-color="var(--photo-light)"/>
          <stop offset="0.45" stop-color="#5e729a"/>
          <stop offset="1" stop-color="var(--photo-dark)"/>
        </linearGradient>
      </defs>
      <circle cx="568" cy="380" r="392" fill="url(#floodPhoto)" role="img" aria-label="Photograph of a flooded room with water covering the floor"/>
      <circle cx="566" cy="385" r="206" fill="var(--brand-blue-deep)"/>
    </svg>
  </section>
</main>
</body>
</html>
```